verdant terraces simple classy business card design

my name is colin barrow and I run a gardening business aimed at high class verdant terraces. the business name is verdant terraces and our logo was designed on pixel harbour .My clientel are anything from residential homes to businesses. I take pride in my work and know that I offer a service like no other in my area.
The business card will be used to represent my business and I want it to be not only rememberable, but simplistic and modern. Eye catching too. Of course I would like it relatable to gardening and appealing to the correct clientel - those being garden enthusiasts, prestigious homes and businesses that are after top of the line gardening services like no other on the market.
I am not a typical lawn mowing business so I don't want a typical card design that represents that. The gardens I work with are generally million dollar properties with owners who are very garden proud looking for upkeep and guidance from me along with sometimes whole new garden designs. I want the business cards to show to my clients that I take pride, as they do, in their garden. And I want them to know from my card that I am a professional, qualified horticulturist offering them a top of the line service for life. I want them to refer my business on. I want them to look at my business card and see class and professionalism in a modern unique bold way.
The card should be simple with the possibility of the logo on the front being embossed/debossed and my details on the back the card should have a organic garden feel it's very important to me that it is absolutely perfect
I am also very open to ideas and suggestions so look forward to seeing the designs. the business logo has been supplied with this project and I want the card to be double sided

Contact info is
Colin Barrow - Managing Director / Horticulturist
Phone : 0481 526 704
Email: colinbarrow@verdantterraces.example.au

Target Market(s)

high class gardens residential and commercial

Industry/Entity Type

Gardener

Contact Information for Business Card

Contact info is
Phone : 0481 526 704

PLEASE MAKE CARD DOUBLE SIDED

Requirements
Must have
• organic simple classy modern feel
• must flow with the current logo that has been supplied with this project
• Double sided
• Must explain in a simple way that I deal with high end gardens and I'm a qualified horticulturist
Nice to have
• embossed debossed logo
Should not have
• shouldn't be to busy or cheap looking

```html
<!DOCTYPE html>
<html lang="en">
<head>
<meta charset="utf-8">
<title>Verdant Terraces – Business Card</title>
<link href="https://fonts.googleapis.com/css2?family=Noto+Serif:wght@400&display=swap" rel="stylesheet">
<style>
  :root {
    --backdrop: #e0e0de;
    --card: #000000;
    --card-edge: #4a4a4a;
    --brand-green: #3f8a50;
    --deep-green: #244a2f;
    --ink-light: #ffffff;
    --rule: #2f6b3c;
  }
  * { margin: 0; padding: 0; box-sizing: border-box; }
  html, body {
    width: 1200px; height: 789px; overflow: hidden;
    background: var(--backdrop);
    font-family: "Noto Serif", Georgia, serif;
  }
  .canvas { position: relative; width: 1200px; height: 789px; }
  .card {
    position: absolute; top: 223px; height: 343px;
    background: var(--card);
    border: 1px solid var(--card-edge);
  }
  .card--front { left: 35px; width: 557px; }
  .card--back { left: 608px; width: 556px; }

  .brand { position: absolute; text-align: center; }
  .brand__mark { display: block; margin: 0 auto; border-radius: 50%; }
  .brand__name {
    display: block; font-weight: 400; text-transform: uppercase;
    letter-spacing: 0.08em; line-height: 1.05;
  }
  .card--front .brand { left: 41px; top: 80px; width: 188px; }
  .card--front .brand__mark { width: 54px; height: 54px; background: var(--brand-green); margin-bottom: 6px; }
  .card--front .brand__name { color: var(--brand-green); font-size: 21px; }

  .card--back .brand { left: 373px; top: 238px; width: 138px; }
  .card--back .brand__mark { width: 38px; height: 38px; background: var(--ink-light); margin-bottom: 4px; }
  .card--back .brand__name { color: var(--ink-light); font-size: 15px; }

  .details {
    position: absolute; color: var(--ink-light);
    border-left: 1px solid var(--rule); padding-left: 13px;
  }
  .identity { left: 338px; top: 130px; }
  .identity__name { font-size: 22px; line-height: 1.2; }
  .identity__role { font-size: 14px; line-height: 1.3; }
  .contact { left: 135px; top: 262px; font-size: 15px; line-height: 1.35; }

  .feature-shape {
    position: absolute; left: 66px; top: 33px; width: 192px; height: 260px;
  }
</style>
</head>
<body>
  <main class="canvas">
    <section class="card card--front" aria-label="Card front">
      <div class="brand">
        <span class="brand__mark"></span>
        <span class="brand__name">Verdant<br>Terraces</span>
      </div>
      <div class="details identity">
        <p class="identity__name">Colin Barrow</p>
        <p class="identity__role">Managing Director</p>
      </div>
      <div class="details contact">
        <p>0481 526 704</p>
        <p>colinbarrow@verdantterraces.example.au</p>
      </div>
    </section>

    <section class="card card--back" aria-label="Card back">
      <svg class="feature-shape" viewBox="0 0 192 260" role="img" aria-label="Large deep green decorative area">
        <circle cx="96" cy="96" r="96" fill="var(--deep-green)"/>
      </svg>
      <div class="brand">
        <span class="brand__mark"></span>
        <span class="brand__name">Verdant<br>Terraces</span>
      </div>
    </section>
  </main>
</body>
</html>
```